Consulting company requires a logo and business card design

I require a logo/business card design for a new company based in Sexsmith Alberta called TallMarsh Integrity Consulting Ltd. I plan to provide the following services: Construction management/inspection for the oil and gas industry, as well as general consulting for Asset Management, fleet management, etc. Have attached a copy of resume for use as guide for

Target Market(s)

Businesses within the oil and gas production, construction and shipping industry

Industry/Entity Type

Oil And Gas

Contact Information for Business Card

Believe should highlight, services offered, safety, quality,

Logo Text

TallMarsh Integrity Consulting (TMIC) ?

Font styles to use
Script

Requirements
Must have
• Open to all options

```html
<!DOCTYPE html>
<html lang="en">
<head>
<meta charset="utf-8">
<title>TallMarsh Integrity Consulting Ltd — Business Card</title>
<link href="https://fonts.googleapis.com/css2?family=Open+Sans:wght@400;600;700&display=swap" rel="stylesheet">
<style>
  :root {
    --backdrop: #2b2622;
    --card: #121212;
    --gold: #f5b400;
    --white: #f2f2f2;
    --muted: #cfcfcf;
    --rule: #3a3a3a;
  }
  * { margin: 0; padding: 0; box-sizing: border-box; }
  html, body { width: 1200px; height: 844px; overflow: hidden; }
  body {
    background: var(--backdrop);
    font-family: "Open Sans", Arial, sans-serif;
    position: relative;
  }
  .card {
    position: absolute;
    top: 272px;
    width: 520px;
    height: 300px;
    background: var(--card);
    border-radius: 4px;
    box-shadow: 0 10px 30px rgba(0,0,0,.45);
    color: var(--white);
  }
  .card--front { left: 45px; }
  .card--back { left: 635px; }

  .brand {
    position: absolute;
    display: flex;
    align-items: center;
    gap: 12px;
  }
  .brand__dot {
    width: 34px; height: 34px;
    border-radius: 50%;
    border: 3px solid var(--gold);
    flex: none;
  }
  .brand__name {
    color: var(--gold);
    font-weight: 600;
    font-size: 24px;
    line-height: 1.1;
  }
  .card--front .brand { left: 78px; top: 48px; }
  .card--back .brand { left: 118px; top: 70px; }

  .person {
    position: absolute;
    right: 292px;
    top: 162px;
    text-align: right;
  }
  .person__name { color: var(--gold); font-size: 20px; font-weight: 400; line-height: 1.1; }
  .person__title { font-size: 13px; color: var(--muted); margin-bottom: 12px; }
  .person__address { font-size: 14px; line-height: 1.25; }

  .divider {
    position: absolute;
    left: 244px; top: 140px;
    width: 1px; height: 110px;
    background: var(--rule);
  }

  .contacts {
    position: absolute;
    left: 262px; top: 142px;
    list-style: none;
    font-size: 13.5px;
    line-height: 1.62;
  }
  .contacts li { display: flex; align-items: center; gap: 9px; }
  .contacts svg { width: 11px; height: 11px; fill: var(--gold); flex: none; }

  .about {
    position: absolute;
    left: 40px; right: 40px; top: 178px;
    text-align: center;
    font-weight: 700;
    font-size: 14px;
    line-height: 1.4;
  }
</style>
</head>
<body>
  <section class="card card--front" aria-label="Business card front">
    <div class="brand">
      <span class="brand__dot"></span>
      <span class="brand__name">TallMarsh Integrity<br>Consulting Ltd</span>
    </div>

    <div class="person">
      <p class="person__name">Daniel Harker</p>
      <p class="person__title">Managing Director</p>
      <p class="person__address">4410, Prairie Ridge Road<br>Sexsmith, AB T0H 3C0</p>
    </div>

    <span class="divider"></span>

    <ul class="contacts">
      <li><svg viewBox="0 0 12 12"><path d="M2.5 1l2 2.2-1 1.3c.7 1.5 1.8 2.6 3.3 3.3l1.3-1 2.2 2-1 1.6C5.8 10.2 1.8 6.2 1 1.7z"/></svg>(780)-555-0142</li>
      <li><svg viewBox="0 0 12 12"><rect x="1" y="4" width="10" height="7" rx="1"/><rect x="3" y="1" width="6" height="3"/></svg>780-555-0187</li>
      <li><svg viewBox="0 0 12 12"><path d="M1 2.5h10v7H1z M1 2.5l5 4 5-4" stroke="#121212" stroke-width=".9"/></svg>hello@tallmarshic.ca</li>
      <li><svg viewBox="0 0 12 12"><circle cx="6" cy="6" r="5"/></svg>www.tallmarshic.ca</li>
    </ul>
  </section>

  <section class="card card--back" aria-label="Business card back">
    <div class="brand">
      <span class="brand__dot"></span>
      <span class="brand__name">TallMarsh Integrity<br>Consulting Ltd</span>
    </div>
    <p class="about">We are a construction management/inspection<br>for the oil and gas industry, as well as general<br>consulting for Asset Management, fleet management.</p>
  </section>
</body>
</html>
```